Redesign of business card for Cedar Ridge Mechanical

We are looking for a new design for our business cards for Cedar Ridge Mechanical. We are a plumbing & HVAC construction company, operating on the West Coast of Canada and USA. Logo attached.
Industry/Entity Type
Construction - Plumbing & HVAC
Contact Information for Business Card
Name, address, phone numbers, email, website address
Look and feel
Each slider illustrates characteristics of the customer's brand and the style your logo design should communicate.

```html
<!DOCTYPE html>
<html lang="en">
<head>
<meta charset="utf-8">
<title>Cedar Ridge Mechanical – Business Card</title>
<link href="https://fonts.googleapis.com/css2?family=Arimo:wght@400;700&display=swap" rel="stylesheet">
<style>
  :root {
    --ink: #1c1c1c;
    --card-dark: #1f1d1d;
    --paper: #ffffff;
    --paper-shade: #e6e6e6;
    --text-light: #f2f2f2;
    --text-muted: #5a5a5a;
    --rule: #444444;
    --stripe: #9a9a9a;
    --web-text: #bdbdbd;
    --bg: #d9d6d2;
  }
  * { box-sizing: border-box; margin: 0; padding: 0; }
  html, body { width: 1200px; height: 900px; overflow: hidden; }
  body {
    background: var(--bg);
    font-family: "Arimo", Arial, sans-serif;
    position: relative;
  }
  .card {
    position: absolute;
    left: 250px;
    width: 700px;
    height: 400px;
    border-radius: 34px;
    overflow: hidden;
    box-shadow: 0 10px 24px rgba(0,0,0,0.25);
  }

  /* ---------- Back side ---------- */
  .card-back {
    top: 35px;
    background: var(--card-dark);
    color: var(--text-light);
    text-align: center;
  }
  .brand {
    display: flex;
    align-items: center;
    gap: 14px;
    font-weight: 700;
    text-transform: uppercase;
    letter-spacing: 1px;
  }
  .brand-square {
    width: 26px;
    height: 26px;
  }
  .card-back .brand {
    position: absolute;
    top: 90px;
    left: 0;
    right: 0;
    justify-content: center;
    font-size: 30px;
    color: var(--text-light);
  }
  .card-back .brand-square { background: var(--text-light); }
  .services-title {
    position: absolute;
    top: 215px;
    left: 0; right: 0;
    font-size: 22px;
    font-weight: 700;
    letter-spacing: 0.5px;
  }
  .services-list {
    position: absolute;
    top: 252px;
    left: 30px; right: 30px;
    font-size: 20px;
    line-height: 31px;
    list-style: none;
  }
  .services-list .dot {
    display: inline-block;
    width: 8px; height: 8px;
    border-radius: 50%;
    background: #8a8a8a;
    margin: 0 8px 3px;
  }

  /* ---------- Front side ---------- */
  .card-front {
    top: 465px;
    background: linear-gradient(110deg, var(--paper) 30%, var(--paper-shade) 100%);
    color: var(--ink);
  }
  .card-front .brand {
    position: absolute;
    top: 95px;
    right: 46px;
    font-size: 26px;
    color: var(--ink);
  }
  .card-front .brand-square { background: var(--ink); }
  .front-rule {
    position: absolute;
    top: 170px;
    left: 40px;
    right: 40px;
    height: 1px;
    background: var(--rule);
  }
  .person {
    position: absolute;
    left: 42px;
    top: 200px;
  }
  .person-name { font-size: 24px; font-weight: 700; letter-spacing: 0.3px; }
  .person-title { font-size: 20px; color: var(--text-muted); margin-top: 4px; }
  .person-rule {
    width: 250px; height: 1px; background: var(--rule);
    margin: 12px 0 12px;
  }
  .contact-line {
    display: flex; align-items: center; gap: 12px;
    font-size: 20px; color: #333; margin-bottom: 6px;
  }
  .contact-line svg { width: 18px; height: 18px; fill: var(--ink); }
  .address {
    position: absolute;
    right: 46px;
    top: 200px;
    text-align: right;
    font-size: 20px;
    line-height: 28px;
    color: #333;
  }
  .front-band { position: absolute; left: 0; top: 0; width: 700px; height: 400px; }
  .web {
    position: absolute;
    right: 40px;
    top: 336px;
    height: 64px;
    width: 290px;
    display: flex;
    align-items: center;
    justify-content: flex-end;
    font-size: 15px;
    letter-spacing: 4px;
    white-space: nowrap;
    color: var(--web-text);
  }
</style>
</head>
<body>

<section class="card card-back">
  <div class="brand"><span class="brand-square"></span>Cedar Ridge Mechanical</div>
  <h2 class="services-title">OUR SERVICES</h2>
  <ul class="services-list">
    <li><span class="dot"></span>Pipefitting Systems<span class="dot"></span>Design Build<span class="dot"></span>Maintenance<span class="dot"></span>Fire Protection</li>
    <li><span class="dot"></span>Control Systems<span class="dot"></span>Energy Recovery &amp; High Efficiency Systems</li>
    <li><span class="dot"></span>Plumbing<span class="dot"></span>HVAC</li>
  </ul>
</section>

<section class="card card-front">
  <svg class="front-band" viewBox="0 0 700 400" aria-hidden="true">
    <rect x="0" y="372" width="352" height="5" fill="var(--stripe)"/>
    <polygon points="0,384 348,384 362,336 700,336 700,400 0,400" fill="var(--card-dark)"/>
  </svg>

  <div class="brand"><span class="brand-square"></span>Cedar Ridge Mechanical</div>
  <div class="front-rule"></div>

  <div class="person">
    <div class="person-name">DANIEL MERCER</div>
    <div class="person-title">President/Founder</div>
    <div class="person-rule"></div>
    <div class="contact-line">
      <svg viewBox="0 0 24 24" aria-hidden="true"><path d="M6.6 10.8a15.1 15.1 0 0 0 6.6 6.6l2.2-2.2a1 1 0 0 1 1-.25 11.4 11.4 0 0 0 3.6.57 1 1 0 0 1 1 1V20a1 1 0 0 1-1 1A17 17 0 0 1 3 4a1 1 0 0 1 1-1h3.5a1 1 0 0 1 1 1c0 1.25.2 2.45.57 3.570a1 1 0 0 1-.25 1z"/></svg>
      213-555-0148
    </div>
    <div class="contact-line">
      <svg viewBox="0 0 24 24" aria-hidden="true"><path d="M2 5h20v14H2zm2 2v.5l8 5 8-5V7zm0 2.9V17h16V9.9l-8 5z"/></svg>
      info@cedarridgemech.com
    </div>
  </div>

  <div class="address">2750 Harbor Line Rd.,<br>Suite #410 Seattle, WA 98134</div>
  <div class="web">www.cedarridgemech.com</div>
</section>

</body>
</html>
```